Meridale Staffing Website

My business has been word of mouth over the last 3 years and has grown. Now I need a website for additional marketing as we have new clients asking for a website.

You have already completed my Logo during an earlier project. I have attached the logo.

We do Staff Augmentation and Operation Support.

What is that?
Staff augmentation is an outsourcing strategy that allows companies to fill specific, temporary roles to achieve business objectives. This staffing method complements existing teams with specific talent, enhancing business capabilities or filling gaps left by members on extended leave.

We work alongside the internal recruiting team to assist clients to meet and exceed financial goals.

```html
<!DOCTYPE html>
<html lang="en">
<head>
<meta charset="utf-8">
<title>Meridale Staffing</title>
<link rel="stylesheet" href="https://fonts.googleapis.com/css2?family=Montserrat:wght@400;500;600;700;800&family=Arimo:ital,wght@0,400;0,700;1,400&display=swap">
<style>
:root{
  --navy:#0d3f6e;
  --ink:#333;
  --footer:#1b1b1b;
  --star:#f5d31c;
  --white:#fff;
}
*{box-sizing:border-box;margin:0;padding:0}
html,body{width:1200px;height:3854px;overflow:hidden;background:var(--white)}
body{position:relative;font-family:"Arimo",Arial,sans-serif;color:var(--ink)}
.abs{position:absolute}

/* Header */
.brand{left:112px;top:26px;display:flex;align-items:center;gap:12px}
.brand-mark{width:62px;height:62px;border-radius:50%;background:var(--navy)}
.brand-name{font-family:"Montserrat",sans-serif;font-weight:700;font-size:28px;color:var(--navy);white-space:nowrap}
.call{left:650px;top:28px;display:flex;align-items:center;gap:10px;font-family:"Montserrat",sans-serif;font-weight:600;font-size:18px;color:var(--navy);white-space:nowrap}
.call-icon{width:46px;height:46px;border:2px solid var(--navy);border-radius:50%;display:flex;align-items:center;justify-content:center}
.quote-btn{left:936px;top:26px;width:152px;height:48px;border-radius:24px;background:var(--navy);color:#fff;font-family:"Montserrat",sans-serif;font-weight:600;font-size:15px;display:flex;align-items:center;justify-content:center}
.nav{top:103px;font-family:"Montserrat",sans-serif;font-weight:500;font-size:14px;color:#222}
.nav a{position:absolute;white-space:nowrap;color:inherit;text-decoration:none}
.nav .active{color:var(--navy);font-weight:600}

/* Hero */
.hero-photo{left:0;top:137px;width:1200px;height:760px;background:linear-gradient(180deg,#3b3c3e 0%,#4a4a4a 45%,#2c2c2c 100%)}
.hero-arrow{top:488px;width:36px;height:36px;border:2px solid #fff;border-radius:50%}
.hero-title{left:0;width:1200px;top:560px;text-align:center;font-family:"Montserrat",sans-serif;font-weight:800;font-size:59px;color:#fff}
.hero-sub{left:0;width:1200px;top:636px;text-align:center;font-family:"Montserrat",sans-serif;font-size:25px;color:#fff}
.pill{background:var(--navy);color:#fff;font-family:"Montserrat",sans-serif;font-weight:500;font-size:17px;border-radius:26px;display:flex;align-items:center;justify-content:center}
.hero-btn{left:518px;top:687px;width:165px;height:48px}

/* Welcome */
.welcome-mark{left:563px;top:870px;width:74px;height:74px;border-radius:50%;background:#fff;border:3px solid var(--navy)}
.welcome-kicker{left:0;width:1200px;top:970px;text-align:center;font-family:"Montserrat",sans-serif;font-size:26px;color:#444}
.welcome-title{left:0;width:1200px;top:1003px;text-align:center;font-family:"Montserrat",sans-serif;font-weight:600;font-size:37px;color:var(--navy)}
.welcome-text{left:245px;width:710px;top:1068px;text-align:center;font-size:13.5px;line-height:27.4px;color:#555}
.welcome-btn{left:517px;top:1256px;width:166px;height:50px}

/* Split services */
.split{left:0;top:1342px;width:1200px;height:568px}
.split-title{font-family:"Montserrat",sans-serif;font-weight:800;font-size:64px;line-height:76px;color:#fff;text-align:center;text-shadow:0 3px 6px rgba(0,0,0,.35)}

/* Service cards */
.card{top:1994px;width:229px;height:253px;border:2px solid #c9c9c9;background:#fff;text-align:center;padding-top:20px}
.card.is-active{background:var(--navy);border-color:var(--navy);color:#fff}
.card svg{display:block;margin:0 auto}
.card h3{font-family:"Montserrat",sans-serif;font-weight:700;font-size:19px;line-height:23px;color:#333;margin-top:12px}
.card p{font-size:13.5px;line-height:21px;color:#555;margin-top:18px}
.card.is-active h3,.card.is-active p{color:#fff}
.chev{top:2077px}

/* Testimonials */
.testimonials{left:0;top:2330px;width:1200px;height:481px}
.t-title{left:0;width:1200px;top:2432px;text-align:center;font-family:"Montserrat",sans-serif;font-weight:500;font-size:37px;color:#fff}
.stars{left:0;width:1200px;top:2494px;text-align:center;font-size:22px;color:var(--star);letter-spacing:1px}
.quote{left:210px;width:780px;top:2542px;text-align:center;font-style:italic;font-size:18px;line-height:31px;color:#fff}
.t-arrow{top:2551px;width:46px;height:46px;border-radius:50%;background:#2d6aa2}
.avatar{border-radius:50%;border:3px solid #fff;background:linear-gradient(160deg,#8a8f96,#4a5560)}
.t-name{left:0;width:1200px;top:2756px;text-align:center;font-family:"Montserrat",sans-serif;font-weight:600;font-size:17px;color:#fff}

/* Team */
.team-title{left:0;width:1200px;top:2860px;text-align:center;font-family:"Montserrat",sans-serif;font-weight:600;font-size:37px;color:var(--navy)}
.team-sub{left:0;width:1200px;top:2917px;text-align:center;font-size:16px;color:#444}
.member{top:2977px;width:312px;height:401px;background:#fff;box-shadow:0 2px 8px rgba(0,0,0,.16);text-align:center;padding-top:28px}
.member .photo{width:168px;height:168px;border-radius:50%;margin:0 auto;background:linear-gradient(160deg,#8c7a6b,#4a3c33)}
.member h4{font-family:"Montserrat",sans-serif;font-weight:600;font-size:18px;color:var(--navy);margin-top:22px}
.member .role{font-size:14px;color:#555;margin-top:4px}
.member p{font-size:13.5px;line-height:23px;color:#666;margin:12px 30px 0}
.member .loc{font-size:15px;font-weight:700;color:var(--navy);margin-top:18px;display:flex;justify-content:center;align-items:center;gap:8px}

/* Footer */
.footer-shape{left:0;top:3440px;width:1200px;height:414px}
.f-brand{left:118px;top:3620px;display:flex;align-items:center;gap:12px}
.f-brand .brand-mark{background:#fff;width:64px;height:64px}
.f-brand .brand-name{color:#fff;font-size:25px}
.f-copy{left:127px;top:3736px;font-size:15px;color:#eee}
.f-head{top:3566px;font-family:"Montserrat",sans-serif;font-weight:500;font-size:22px;color:#fff}
.f-item{display:flex;gap:14px;align-items:center}
.f-circle{width:42px;height:42px;border:2px solid #fff;border-radius:50%;display:flex;align-items:center;justify-content:center;flex:none}
.f-item b{display:block;font-family:"Montserrat",sans-serif;font-weight:600;font-size:16px;color:#fff}
.f-item span{display:block;font-size:13px;line-height:19px;color:#eee}
.f-links{left:746px;top:3612px;font-size:15px;color:#fff;line-height:34.5px;list-style:none}
.f-links li::before{content:"›";font-size:20px;margin-right:18px}
.follow{left:943px;display:flex;align-items:center;gap:14px}
.follow .dot{width:36px;height:36px;border-radius:50%;background:#fff}
.follow small{display:block;font-size:12px;color:#eee;font-family:"Montserrat",sans-serif}
.follow strong{display:block;font-weight:400;font-size:16px;color:#fff;font-family:"Montserrat",sans-serif;letter-spacing:.5px}
</style>
</head>
<body>

<!-- Header -->
<div class="abs brand"><div class="brand-mark"></div><div class="brand-name">Meridale Staffing</div></div>
<div class="abs call">
  <div class="call-icon"><svg width="18" height="18" viewBox="0 0 24 24"><path fill="#0d3f6e" d="M6.6 10.8a15 15 0 0 0 6.6 6.6l2.2-2.2c.3-.3.7-.4 1-.2 1.1.4 2.3.6 3.6.6.6 0 1 .4 1 1V20c0 .6-.4 1-1 1A17 17 0 0 1 3 4c0-.6.4-1 1-1h3.5c.6 0 1 .4 1 1 0 1.3.2 2.5.6 3.6.1.3 0 .7-.2 1z"/></svg></div>
  CALL US : 000-555-0142
</div>
<div class="abs quote-btn">GET A QUOTE</div>
<nav class="abs nav">
  <a class="active" style="left:454px">HOME</a>
  <a style="left:546px">ABOUT US</a>
  <a style="left:668px">SERVICES</a>
  <a style="left:787px">TEAM</a>
  <a style="left:877px">PARTNER</a>
  <a style="left:995px">CONTACT US</a>
</nav>

<!-- Hero -->
<div class="abs hero-photo" role="img" aria-label="Photo of a smiling business team standing together in an office"></div>
<div class="abs hero-arrow" style="left:65px"><svg width="32" height="32" viewBox="0 0 32 32"><path d="M18 10l-6 6 6 6" stroke="#fff" stroke-width="2" fill="none"/></svg></div>
<div class="abs hero-arrow" style="left:1094px"><svg width="32" height="32" viewBox="0 0 32 32"><path d="M14 10l6 6-6 6" stroke="#fff" stroke-width="2" fill="none"/></svg></div>
<h1 class="abs hero-title">MERIDALE STAFFING</h1>
<div class="abs hero-sub">SED UT PERSPICIATIS UNDE OMNIS ISTE NATUS</div>
<div class="abs pill hero-btn">READ MORE</div>
<svg class="abs" style="left:0;top:760px" width="1200" height="150" viewBox="0 0 1200 150">
  <path d="M0 20 Q600 200 1200 20 L1200 150 L0 150Z" fill="#fff"/>
</svg>

<!-- Welcome -->
<div class="abs welcome-mark"></div>
<div class="abs welcome-kicker">WELCOME TO</div>
<h2 class="abs welcome-title">MERIDALE STAFFING</h2>
<p class="abs welcome-text">Sed ut perspiciatis unde omnis iste natus error sit voluptatem accusantium doloremque laudantium, totam rem aperiam, eaque ipsa quae ab illo inventore veritatis et quasi architecto beatae vitae dicta sunt explicabo. Nemo enim ipsam voluptatem quia voluptas sit aspernatur aut odit aut fugit, sed quia consequuntur magni dolores eos qui ratione voluptatem sequi nesciunt. Neque porro quisquam est, qui dolorem ipsum quia dolor sit amet, consectetur, adipisci velit, sed quia non numquam eius modi tempora incidunt ut labore et dolore magnam aliquam volupta tem accusantium doloremque laudantium quaerat voluptatem.</p>
<div class="abs pill welcome-btn">READ MORE</div>

<!-- Split services -->
<svg class="abs split" viewBox="0 0 1200 568">
  <polygon points="0,0 600,48 600,520 0,568" fill="#0f4475"/>
  <polygon points="600,48 1200,0 1200,568 600,520" fill="#5e6064"/>
</svg>
<div class="abs" role="img" aria-label="Engineers at work, blue tinted photo" style="left:0;top:1342px;width:600px;height:568px"></div>
<div class="abs" role="img" aria-label="Support operator with headset at monitors, grey tinted photo" style="left:600px;top:1342px;width:600px;height:568px"></div>
<div class="abs split-title" style="left:0;width:576px;top:1548px">STAFF<br>AUGMENTATION</div>
<div class="abs split-title" style="left:700px;width:460px;top:1548px">OPERATION<br>SUPPORT</div>

<!-- Service cards -->
<svg class="abs chev" style="left:52px" width="40" height="70" viewBox="0 0 40 70"><path d="M36 2 2 35l34 33" stroke="#999" stroke-width="1.5" fill="none"/></svg>
<svg class="abs chev" style="left:1108px" width="40" height="70" viewBox="0 0 40 70"><path d="M4 2l34 33L4 68" stroke="#999" stroke-width="1.5" fill="none"/></svg>

<div class="abs card is-active" style="left:111px">
  <svg width="86" height="86" viewBox="0 0 86 86" fill="none" stroke="#fff" stroke-width="2"><rect x="10" y="8" width="44" height="58"/><path d="M18 20h28M18 30h18M18 52h14"/><circle cx="46" cy="44" r="16"/><path d="M38 44l6 6 10-12M57 55l16 16"/></svg>
  <h3>Background<br>Verification</h3>
  <p>Sed ut perspiciatis unde<br>omnis iste natuslosi</p>
</div>
<div class="abs card" style="left:361px">
  <svg width="86" height="86" viewBox="0 0 86 86" fill="none" stroke="#0d3f6e" stroke-width="2"><circle cx="43" cy="26" r="14"/><circle cx="43" cy="26" r="6"/><path d="M43 8v4M43 40v4M25 26h4M57 26h4"/><rect x="16" y="46" width="54" height="30"/><path d="M10 76h66"/></svg>
  <h3>Handling of<br>Work Projects</h3>
  <p>Sed ut perspiciatis unde<br>omnis iste natuslosi</p>
</div>
<div class="abs card" style="left:611px">
  <svg width="86" height="86" viewBox="0 0 86 86" fill="none" stroke="#0d3f6e" stroke-width="2"><rect x="6" y="8" width="74" height="52"/><path d="M6 16h74M48 50V36M56 50V28M64 50V32M72 50V24"/><circle cx="24" cy="34" r="6"/><path d="M16 78V50h16v28"/></svg>
  <h3>Performance<br>Management</h3>
  <p>Sed ut perspiciatis unde<br>omnis iste natuslosi</p>
</div>
<div class="abs card" style="left:861px">
  <svg width="86" height="86" viewBox="0 0 86 86" fill="none" stroke="#0d3f6e" stroke-width="2"><circle cx="43" cy="22" r="12"/><circle cx="43" cy="22" r="5"/><path d="M43 34v10M24 50V44h38v6"/><rect x="12" y="50" width="24" height="30"/><rect x="50" y="50" width="24" height="30"/><path d="M18 60h12M18 68h12M56 60h12M56 68h12"/></svg>
  <h3>Feedback<br>Mechanism</h3>
  <p>Sed ut perspiciatis unde<br>omnis iste natuslosi</p>
</div>

<!-- Testimonials -->
<svg class="abs testimonials" viewBox="0 0 1200 481">
  <polygon points="0,0 600,50 1200,0 1200,481 0,481" fill="#0d3f6e"/>
  <polygon points="0,0 600,50 1200,0 1200,10 600,58 0,10" fill="#6b6d70"/>
</svg>
<div class="abs" role="img" aria-label="Faint background photo of people working, under a blue tint" style="left:0;top:2388px;width:1200px;height:422px"></div>
<h2 class="abs t-title">TESTIMONIALS</h2>
<div class="abs stars">★★★★☆</div>
<p class="abs quote">Sed ut perspiciatis unde omnis iste natus error sit voluptatem accusantium doloremque lauda ntium, totam rem aperiam, eaque ipsa quae ab illo inventore veritatis</p>
<div class="abs t-arrow" style="left:113px"><svg width="46" height="46" viewBox="0 0 46 46"><path d="M26 15l-8 8 8 8" stroke="#fff" stroke-width="3" fill="none"/></svg></div>
<div class="abs t-arrow" style="left:1040px"><svg width="46" height="46" viewBox="0 0 46 46"><path d="M20 15l8 8-8 8" stroke="#fff" stroke-width="3" fill="none"/></svg></div>
<div class="abs avatar" role="img" aria-label="Client portrait" style="left:436px;top:2642px;width:86px;height:86px;opacity:.6"></div>
<div class="abs avatar" role="img" aria-label="Client portrait" style="left:550px;top:2632px;width:100px;height:100px;background:linear-gradient(160deg,#c59a78,#5a3a28)"></div>
<div class="abs avatar" role="img" aria-label="Client portrait" style="left:662px;top:2642px;width:86px;height:86px;opacity:.6"></div>
<div class="abs t-name">-DANA WHITLOW</div>

<!-- Team -->
<h2 class="abs team-title">OUR TEAM</h2>
<p class="abs team-sub">Sed ut perspiciatis unde omnis iste natus error sit voluptatem accusantium</p>

<div class="abs member" style="left:111px">
  <div class="photo" role="img" aria-label="Portrait of a team member"></div>
  <h4>DANA WHITLOW</h4><div class="role">Business Partner</div>
  <p>Sed ut perspiciatis unde omnis iste natus error sit voluptatem accusant eium doloremque</p>
  <div class="loc"><svg width="11" height="15" viewBox="0 0 11 15"><path d="M5.5 0A5.5 5.5 0 0 0 0 5.5C0 9.6 5.5 15 5.5 15S11 9.6 11 5.5A5.5 5.5 0 0 0 5.5 0zm0 7.6a2 2 0 1 1 0-4 2 2 0 0 1 0 4z" fill="#0d3f6e"/></svg>Sed ut perspiciatis unde</div>
</div>
<div class="abs member" style="left:443px">
  <div class="photo" role="img" aria-label="Portrait of a team member" style="background:linear-gradient(160deg,#b08868,#4c3426)"></div>
  <h4>DANA WHITLOW</h4><div class="role">Business Partner</div>
  <p>Sed ut perspiciatis unde omnis iste natus error sit voluptatem accusant eium doloremque</p>
  <div class="loc"><svg width="11" height="15" viewBox="0 0 11 15"><path d="M5.5 0A5.5 5.5 0 0 0 0 5.5C0 9.6 5.5 15 5.5 15S11 9.6 11 5.5A5.5 5.5 0 0 0 5.5 0zm0 7.6a2 2 0 1 1 0-4 2 2 0 0 1 0 4z" fill="#0d3f6e"/></svg>Sed ut perspiciatis unde</div>
</div>
<div class="abs member" style="left:775px">
  <div class="photo" role="img" aria-label="Portrait of a team member" style="background:linear-gradient(160deg,#7a6a5e,#2e2622)"></div>
  <h4>DANA WHITLOW</h4><div class="role">Business Partner</div>
  <p>Sed ut perspiciatis unde omnis iste natus error sit voluptatem accusant eium doloremque</p>
  <div class="loc"><svg width="11" height="15" viewBox="0 0 11 15"><path d="M5.5 0A5.5 5.5 0 0 0 0 5.5C0 9.6 5.5 15 5.5 15S11 9.6 11 5.5A5.5 5.5 0 0 0 5.5 0zm0 7.6a2 2 0 1 1 0-4 2 2 0 0 1 0 4z" fill="#0d3f6e"/></svg>Sed ut perspiciatis unde</div>
</div>

<!-- Footer -->
<svg class="abs footer-shape" viewBox="0 0 1200 414">
  <path d="M0 138 Q520 -40 1200 138 L1200 414 L0 414Z" fill="#1b1b1b"/>
</svg>
<div class="abs f-brand"><div class="brand-mark"></div><div class="brand-name">Meridale Staffing</div></div>
<div class="abs f-copy">© Copyrights 2022.All Rights Reserved.</div>

<div class="abs f-head" style="left:477px">ADDRESS</div>
<div class="abs f-head" style="left:746px">LINKS</div>
<div class="abs f-head" style="left:947px">FOLLOW</div>

<div class="abs f-item" style="left:470px;top:3612px">
  <div class="f-circle"><svg width="12" height="16" viewBox="0 0 11 15"><path d="M5.5 0A5.5 5.5 0 0 0 0 5.5C0 9.6 5.5 15 5.5 15S11 9.6 11 5.5A5.5 5.5 0 0 0 5.5 0zm0 7.6a2 2 0 1 1 0-4 2 2 0 0 1 0 4z" fill="#fff"/></svg></div>
  <div><b>ADDRESS</b><span>25 Lorem Ipsum Dummy<br>Lorem Ipsum</span></div>
</div>
<div class="abs f-item" style="left:470px;top:3694px">
  <div class="f-circle"><svg width="16" height="16" viewBox="0 0 24 24"><path fill="#fff" d="M6.6 10.8a15 15 0 0 0 6.6 6.6l2.2-2.2c.3-.3.7-.4 1-.2 1.1.4 2.3.6 3.6.6.6 0 1 .4 1 1V20c0 .6-.4 1-1 1A17 17 0 0 1 3 4c0-.6.4-1 1-1h3.5c.6 0 1 .4 1 1 0 1.3.2 2.5.6 3.6.1.3 0 .7-.2 1z"/></svg></div>
  <div><b>PHONE</b><span>000-555-0142</span></div>
</div>
<div class="abs f-item" style="left:470px;top:3762px">
  <div class="f-circle"><svg width="16" height="12" viewBox="0 0 16 12"><path d="M0 0h16v12H0z" fill="#fff"/><path d="M0 0l8 6 8-6" stroke="#1b1b1b" stroke-width="1.5" fill="none"/></svg></div>
  <div><b>EMAIL</b><span>hello@meridalestaffing.com</span></div>
</div>

<ul class="abs f-links">
  <li>Home</li><li>About Us</li><li>Services</li><li>Team</li><li>Partner</li><li>Contact Us</li>
</ul>

<div class="abs follow" style="top:3620px"><div class="dot"></div><div><small>Like us on</small><strong>Connectly</strong></div></div>
<div class="abs follow" style="top:3678px"><div class="dot"></div><div><small>Follow us on</small><strong>Chirper</strong></div></div>
<div class="abs follow" style="top:3736px"><div class="dot"></div><div><small>Follow us on</small><strong>WorkLink</strong></div></div>

</body>
</html>
```